SkyvornQ Business Cards and Stationary Design

Need a design for our business cards and stationary. I want to carry on the theme of the logo. I want the business cards to have a design on the back. I would like the business cards and the stationary to carry the same theme, design scheme, and branding

Target Market(s)

Airlines and Maintenance Facilities

Industry/Entity Type

Aviation

Contact Information for Business Card

Name
Position Title
Address: 4827 Trellis Hollow Road, Fort Pierce, Florida, 34951
Office Number
Mobile Number
Email
Website

Font styles to use
Serif
Sans Serif

Colors

Designer to choose colors to be used in the design.

```html
<!DOCTYPE html>
<html lang="en">
<head>
<meta charset="utf-8">
<title>SkyvornQ Business Card</title>
<link href="https://fonts.googleapis.com/css2?family=Open+Sans:wght@400;600;700&display=swap" rel="stylesheet">
<style>
  :root {
    --stage: #666666;
    --navy: #0c2f6b;
    --sky: #1e90d8;
    --paper: #fbfbfb;
    --ink: #333333;
    --white: #ffffff;
  }
  * { margin: 0; padding: 0; box-sizing: border-box; }
  html, body { width: 1125px; height: 1200px; overflow: hidden; background: var(--stage); }
  body { position: relative; font-family: "Open Sans", Arial, sans-serif; }

  .card {
    position: absolute;
    top: 252px;
    width: 398px;
    height: 694px;
    border-radius: 199px 199px 16px 16px / 199px 199px 16px 16px;
    overflow: hidden;
    box-shadow: 0 2px 6px rgba(0,0,0,0.35);
  }
  .card--front { left: 132px; background: radial-gradient(circle at 50% 55%, #ffffff 0%, var(--paper) 60%, #f2f2f2 100%); }
  .card--back { left: 596px; background: var(--navy); }

  .brand-ring {
    position: absolute;
    left: 50%;
    top: 350px;
    width: 112px;
    height: 112px;
    margin-left: -56px;
    border-radius: 50%;
    border: 8px solid var(--sky);
  }
  .card--front .brand-ring { top: 98px; border-color: var(--navy); }
  .card--back .brand-ring { top: 100px; border-color: var(--white); }

  .brand-name {
    position: absolute;
    left: 0; right: 0;
    top: 222px;
    text-align: center;
    font-weight: 700;
    font-size: 36px;
    letter-spacing: 7px;
    padding-left: 7px;
    line-height: 1;
  }
  .card--front .brand-name { color: var(--navy); }
  .card--back .brand-name { color: var(--white); top: 220px; }

  .name-band {
    position: absolute;
    left: 0; right: 0;
    top: 334px;
    height: 70px;
    background: var(--navy);
    border-top: 4px solid var(--sky);
    color: var(--white);
    text-align: center;
  }
  .person-name { font-weight: 700; font-size: 22px; line-height: 1; margin-top: 9px; letter-spacing: 0.3px; }
  .person-title { font-weight: 400; font-size: 19px; line-height: 1; margin-top: 8px; }

  .address {
    position: absolute;
    left: 33px;
    top: 490px;
    color: var(--ink);
    font-size: 17px;
    line-height: 26px;
  }
  .contacts {
    position: absolute;
    left: 37px;
    top: 568px;
    list-style: none;
    color: var(--ink);
    font-size: 17px;
    line-height: 22.7px;
  }
  .contacts li { display: flex; align-items: center; }
  .contacts svg { width: 14px; height: 14px; margin-right: 11px; fill: var(--navy); flex: none; }

  .web-rule {
    position: absolute;
    left: 22px; right: 22px;
    top: 638px;
    display: flex;
    align-items: center;
    justify-content: space-between;
    color: var(--white);
    font-size: 18px;
    letter-spacing: 3px;
  }
  .web-rule::before, .web-rule::after {
    content: "";
    width: 58px;
    height: 1px;
    background: var(--white);
  }
</style>
</head>
<body>
  <section class="card card--front">
    <div class="brand-ring"></div>
    <div class="brand-name">SKYVORNQ</div>
    <div class="name-band">
      <div class="person-name">DARA WHITLOW</div>
      <div class="person-title">President and CEO</div>
    </div>
    <p class="address">4827 Trellis Hollow Road,<br>Fort Pierce, Florida, 34951</p>
    <ul class="contacts">
      <li><svg viewBox="0 0 16 16"><path d="M3.6 1l2.4 3-1.3 1.6c.8 1.8 2.2 3.3 4 4.2l1.6-1.3 3 2.4-1.4 2.6C6.6 13.4 2.5 9.3 1 3.6z"/></svg>001 318 4470</li>
      <li><svg viewBox="0 0 16 16"><path d="M4 0h8a1 1 0 0 1 1 1v14a1 1 0 0 1-1 1H4a1 1 0 0 1-1-1V1a1 1 0 0 1 1-1zm.6 1.6v11h6.8v-11zM8 13.4a.8.8 0 1 0 0 1.6.8.8 0 0 0 0-1.6z"/></svg>001 318 4470</li>
      <li><svg viewBox="0 0 16 16"><path d="M0 3h16v1L8 9 0 4zm0 2.6l8 5 8-5V13H0z"/></svg>info@skyvornq.com</li>
      <li><svg viewBox="0 0 16 16"><path d="M8 0a8 8 0 1 0 0 16A8 8 0 0 0 8 0zm-1 1.6V4H4.6A6.5 6.5 0 0 1 7 1.6zm2 0A6.5 6.5 0 0 1 11.4 4H9zM3.8 5.5H7v2H1.6a6 6 0 0 1 .6-2zm5.2 0h3.2a6 6 0 0 1 .6 2H9zm-7.4 3.5H7v2H3.8a6 6 0 0 1-1.6-2zm7.4 0h5.4a6 6 0 0 1-1.6 2H9zM4.6 12.4H7v2a6.5 6.5 0 0 1-2.4-2zm4.4 0h2.4A6.5 6.5 0 0 1 9 14.4z"/></svg>www.skyvornq.com</li>
    </ul>
  </section>

  <section class="card card--back">
    <div class="brand-ring"></div>
    <div class="brand-name">SKYVORNQ</div>
    <div class="web-rule">www.skyvornq.com</div>
  </section>
</body>
</html>
```